Bench Advertisement - We Buy Houses Design Needed

Need a catchy, simple but elegant design for bus benches to advertise our company.

We need our website, or phone number, and a smal description (1-2 bulletpoints of what we do and what we offer)

The tricky part is for the designer to fit everything and make the website name as part of the title and fitting everything so that people passing by on the street can see what we offer.

Our website is quickdealhomebuyer.com - (916) 555-0143

Something simple but something that catches the eye of walking pedestrians, and drivers driving by the bench.

Our company buys houses, any condition, any situation, we buy houses for cash and close quickly. You can use this description to create a few bulletpoints however you like. Must follow dimensions in attachment.

Target Market(s)

People in foreclosure, about to lose their homes, people that need a quick cash sale of their property

Industry/Entity Type

Real Estate

Requirements
Must have
• catchy, website name, phone number, few brief bulletpoints about what we offer, colors that will catch peoples eye while walking or driving - advertisement will be placed on bus benches - visit our website to see the type of houses we buy - Also have more work for winner of design with possible bonuses
Nice to have
• Feel free to use description or images on our website - make sure the description is just bullet points and it fits with the overall theme / size of the advertisement - Bold bright colors - put yourself in their shoes (if you were going through financial difficulties and about to lose your house to foreclosure or auction, what would you want to see to pick up the phone and call us for a quick sale of your house?) (or if you have a house that you are having a problem with, problem renters, unkept/beat up house, what would make you want to call us and sell your house to us?)

```html
<!DOCTYPE html>
<html lang="en">
<head>
<meta charset="utf-8">
<title>Quick Deal Home Buyer – Bench Advertisement</title>
<link href="https://fonts.googleapis.com/css2?family=Open+Sans:wght@400;600;700&family=PT+Sans+Narrow:wght@700&display=swap" rel="stylesheet">
<style>
  :root {
    --page: #2b2b2b;
    --teal-top: #70b7c0;
    --teal-bottom: #3c8a97;
    --teal-text: #3b8b98;
    --orange: #f07a12;
    --white: #ffffff;
  }
  * { margin: 0; padding: 0; box-sizing: border-box; }
  html, body {
    width: 1200px;
    height: 768px;
    overflow: hidden;
    background: var(--page);
  }
  .bench-ad {
    position: absolute;
    left: 30px;
    top: 226px;
    width: 1200px;
    height: 333px;
    transform: scale(0.95);
    transform-origin: top left;
    overflow: hidden;
    background: var(--white);
  }
  .bench-ad__backdrop {
    position: absolute;
    inset: 0;
    width: 100%;
    height: 100%;
  }
  .brand-name {
    position: absolute;
    left: 40px;
    top: 96px;
    width: 336px;
    text-align: center;
    font-family: "Open Sans", sans-serif;
    font-weight: 400;
    font-size: 24px;
    letter-spacing: 0.5px;
    color: var(--white);
  }
  .contact {
    position: absolute;
    right: 45px;
    top: 36px;
    text-align: right;
    color: var(--white);
    font-family: "Open Sans", sans-serif;
  }
  .contact__web {
    font-weight: 600;
    font-size: 33px;
    line-height: 44px;
  }
  .contact__phone {
    font-weight: 700;
    font-size: 46px;
    line-height: 60px;
  }
  .offer-list {
    position: absolute;
    left: 0;
    right: 0;
    top: 226px;
    list-style: none;
    text-align: center;
    font-family: "PT Sans Narrow", sans-serif;
    font-weight: 700;
    font-size: 32px;
    line-height: 41px;
    color: var(--teal-text);
    text-transform: uppercase;
  }
  .offer-list__item::before {
    content: "";
    display: inline-block;
    width: 20px;
    height: 20px;
    margin-right: 10px;
    background: var(--teal-text);
    vertical-align: 1px;
  }
</style>
</head>
<body>
  <section class="bench-ad">
    <svg class="bench-ad__backdrop" viewBox="0 0 1200 333" preserveAspectRatio="none" aria-hidden="true">
      <defs>
        <linearGradient id="teal-band" x1="0" y1="0" x2="0" y2="1">
          <stop offset="0" stop-color="var(--teal-top)"/>
          <stop offset="1" stop-color="var(--teal-bottom)"/>
        </linearGradient>
      </defs>
      <rect width="1200" height="333" fill="url(#teal-band)"/>
      <path d="M0 246 Q600 96 1200 246 L1200 333 L0 333 Z" fill="var(--white)"/>
      <path d="M50 244 Q600 122 1160 244" fill="none" stroke="var(--orange)" stroke-width="6"/>
    </svg>

    <div class="brand-name">QUICK DEAL HOME BUYER</div>

    <div class="contact">
      <p class="contact__web">QUICKDEALHOMEBUYER.COM</p>
      <p class="contact__phone">Cell (916) 555-0143</p>
    </div>

    <ul class="offer-list">
      <li class="offer-list__item">We buy houses for cash &amp; close quickly</li>
      <li class="offer-list__item">Our company buys houses, any condition, any situation</li>
    </ul>
  </section>
</body>
</html>
```